Tax Preparation flyer for LedgerVale Corp.

My Client would like a one page PDF flyer to promote upcoming tax season in Canada. This firm is affordable and all virtual. I have attached a copy of their logo and a word document with the proposed wording for the flyer. Please feel free to change if you have better suggestions.

Target Market(s)

individuals in canada

Colors
0054AA
0677BA
7BADD7
CADEEF
E8F1F8

```html
<!DOCTYPE html>
<html lang="en">
<head>
<meta charset="utf-8">
<title>LedgerVale Corp. – Tax Season Flyer</title>
<link href="https://fonts.googleapis.com/css2?family=Poppins:wght@400;500;600;700;800&display=swap" rel="stylesheet">
<style>
:root{
  --blue:#1a99d8;
  --slate:#41657c;
  --charcoal:#36383c;
  --ink:#333437;
  --white:#ffffff;
  --stage:#f2f2f2;
}
*{margin:0;padding:0;box-sizing:border-box}
html,body{width:1200px;height:1200px;overflow:hidden;background:var(--stage);font-family:'Poppins',sans-serif;color:var(--ink)}
.flyer{position:absolute;left:172px;top:0;width:856px;height:1200px;background:var(--white);overflow:hidden}
.abs{position:absolute}
.shapes{left:0;top:0}
.photo{left:193px;top:268px;width:663px;height:404px;background:linear-gradient(120deg,#e9eef2 0%,#cfd8de 45%,#f4f6f7 100%)}
.headline{right:31px;top:20px;font-size:104px;font-weight:700;color:var(--blue);line-height:1;letter-spacing:-1px}
.subhead{right:31px;top:115px;font-size:33px;font-weight:500;line-height:1.2;color:var(--ink)}
.intro{right:31px;top:166px;width:660px;text-align:right;font-size:13.6px;line-height:21px}
.hl{color:var(--blue);font-weight:700}
.portal{left:29px;top:699px;width:805px;font-size:13.6px;line-height:21px}
.meet-band{left:0;top:753px;width:856px;height:60px;background:var(--charcoal);color:var(--white);font-weight:700;font-size:16px;line-height:24px;padding:6px 29px}
.price-box{left:45px;top:845px;width:452px;height:88px;background:var(--charcoal);border-radius:6px}
.price-tab{left:132px;top:831px;width:276px;height:44px}
.price-title{left:132px;top:829px;width:276px;text-align:center;color:var(--white);font-weight:700;font-size:30px;line-height:44px}
.price-label{left:54px;top:877px;color:var(--white);font-size:13.5px}
.price-amount{left:58px;top:893px;color:var(--white);font-size:34px;font-weight:700;line-height:44px}
.addon{left:205px;top:880px;width:284px;height:46px;background:var(--white);border-radius:5px;text-align:center;font-size:13.5px;line-height:20px;padding-top:3px;white-space:nowrap}
.addon b{font-weight:700}
.divider{left:527px;top:855px;width:2px;height:70px;background:var(--ink)}
.complex{left:558px;top:846px;width:262px;font-size:13.6px;line-height:21px;text-align:justify}
.behind{left:0;width:856px;top:946px;text-align:center;font-size:21px;font-weight:700}
.save-box{left:78px;top:984px;width:700px;height:27px;border:1.5px solid var(--ink);border-radius:4px;box-shadow:2px 2px 0 var(--ink);text-align:center;font-size:13.4px;line-height:24px;white-space:nowrap;overflow:hidden}
.refund{left:29px;top:1022px;width:805px;font-size:13.6px;line-height:21px}
.breathe{left:29px;top:1070px;font-size:23.5px;font-weight:700}
.contact-title{left:31px;top:1121px;color:var(--white);font-weight:700;font-size:18px;line-height:25px}
.contact-item{top:1156px;color:var(--white);font-size:14px;display:flex;align-items:center;gap:7px;white-space:nowrap}
.email{left:29px}
.phone{left:219px}
.brand{right:29px;top:1092px;text-align:center;color:var(--ink);font-weight:700;font-size:31px;line-height:34px}
</style>
</head>
<body>
<main class="flyer">
  <svg class="abs shapes" width="856" height="1200" viewBox="0 0 856 1200" aria-hidden="true">
    <polygon points="0,0 56,0 233,268 0,268" fill="var(--blue)"/>
  </svg>
  <div class="abs photo" role="img" aria-label="Businessman in a suit meditating calmly at his laptop in a bright office"></div>
  <svg class="abs shapes" width="856" height="1200" viewBox="0 0 856 1200" aria-hidden="true">
    <polygon points="0,83 82,83 206,268 90,672 0,672" fill="var(--slate)"/>
    <polygon points="193,268 90,672 458,672" fill="#5a5c60" opacity="0.45"/>
    <polygon points="0,672 665,672 679,694 0,694" fill="var(--blue)"/>
    <polygon points="665,672 856,672 856,694 679,694" fill="var(--charcoal)"/>
    <polygon points="0,1121 179,1121 199,1146 0,1146" fill="var(--blue)"/>
    <polygon points="0,1146 359,1146 395,1200 0,1200" fill="var(--charcoal)"/>
    <polygon points="359,1146 374,1146 420,1200 395,1200" fill="var(--blue)"/>
  </svg>

  <h1 class="abs headline">Relax!</h1>
  <h2 class="abs subhead">We’ve Got Your Taxes Covered!</h2>
  <p class="abs intro">Our tax preparers have over <span class="hl">20 years</span> experience and worked both in public accounting<br>firms as well as specialized tax.&nbsp; Our tax services are virtual, so you don’t have to take the<br>time for a personal visit. We take care of everything and can access all your tax slips<br>from CRA website directly into our tax software. All signing is done via <span class="hl">SignFlow</span>.</p>

  <p class="abs portal">You can fill and submit the appropriate forms, along with all your other documents, in our secure client portal. It’s<br>important that we understand your situation and any changes in your situation from the past year.</p>

  <p class="abs meet-band">If you have a complex tax situation and would like to discuss it, we can meet in virtually over<br>MeetLine or TalkRoom.</p>

  <div class="abs price-box"></div>
  <svg class="abs price-tab" width="276" height="44" viewBox="0 0 276 44" aria-hidden="true">
    <path d="M0,14 Q6,0 20,0 L256,0 Q270,0 276,14 Z" fill="var(--slate)"/>
    <path d="M22,0 L254,0 Q246,40 214,44 L62,44 Q30,40 22,0 Z" fill="var(--blue)"/>
  </svg>
  <div class="abs price-title">Pricing</div>
  <div class="abs price-label">Personal Tax Return</div>
  <div class="abs price-amount">$100.00</div>
  <div class="abs addon">Add a business or rental schedule<br><b>$125</b> per business or rental property.</div>
  <div class="abs divider"></div>
  <p class="abs complex">More complex tax returns will be assessed based on the complexity of the return and you will be advised before we start.</p>

  <h3 class="abs behind">Did you fall behind in <span class="hl">filing your income tax</span>?</h3>
  <div class="abs save-box">Save <span class="hl">20%</span> when you file <span class="hl">3 or more</span> years with us.&nbsp; We can do <span class="hl">back to 2012</span> for filing of tax returns.</div>
  <p class="abs refund">If you expect a refund, the earlier you file the sooner you will receive your refund.&nbsp; Our average turn around time prior<br>to April is <span class="hl">a couple of days</span>.</p>
  <p class="abs breathe">So you can start <span class="hl">to breathe easy</span>.</p>

  <div class="abs contact-title">Contact us:</div>
  <div class="abs contact-item email">
    <svg width="19" height="19" viewBox="0 0 20 20" aria-hidden="true"><circle cx="10" cy="10" r="9" fill="none" stroke="#fff" stroke-width="1.3"/><rect x="5.5" y="6.8" width="9" height="6.4" fill="none" stroke="#fff" stroke-width="1.2"/><path d="M5.5,6.8 L10,10.6 L14.5,6.8" fill="none" stroke="#fff" stroke-width="1.2"/></svg>
    hello@ledgervale.ca
  </div>
  <div class="abs contact-item phone">
    <svg width="19" height="19" viewBox="0 0 20 20" aria-hidden="true"><circle cx="10" cy="10" r="9" fill="none" stroke="#fff" stroke-width="1.3"/><path d="M7,5.5 L8.6,5.5 L9.3,8 L8.3,9 Q9.3,11.2 11,11.7 L12,10.7 L14.5,11.4 L14.5,13 Q13.8,14.3 12.3,14.2 Q6.2,13 5.8,7 Q5.8,5.8 7,5.5 Z" fill="none" stroke="#fff" stroke-width="1.1"/></svg>
    555 010 0199
  </div>

  <div class="abs brand">LedgerVale<br>Corp.</div>
</main>
</body>
</html>
```